Nitrogen generation business website

Project Overview:
This project aims to create a sleek, user-friendly, and responsive WordPress template for Flo7K3, a provider of Nitrogen generation solutions. The site will serve as a primary touchpoint for customers and businesses looking to enquire about or purchase Flo7K3 products and services. The website should clearly communicate the benefits of working with Flo7K3 as a distributor, focusing on ease of access, expert consultation, and fast, reliable service.
Target Audience:
• Industrial companies seeking Nitrogen solutions.
• Engineers, facility managers, and purchasing teams in need of high-quality Nitrogen systems.
• Partners or businesses seeking to collaborate or purchase through a distributor.
Key Objectives:
1. Establish Flo7K3’s Brand Identity: Use the bold, energetic logo and branding of Flo7K3 (as seen in the uploaded logo) throughout the design. Ensure the brand’s personality shines, with a focus on modernity, reliability, and innovation.
2. Showcase Products and Solutions: Display detailed product categories and descriptions, emphasising the solutions Flo7K3 offers.
3. Lead Generation: Incorporate contact forms, quote requests, and easy-to-find CTAs to convert visitors into leads.
4. User-Centric Design: The design must be intuitive and user-friendly, providing a smooth experience across desktop and mobile devices.
Design Requirements:
1. Home Page:
• Hero Banner: A dynamic, visually engaging hero banner featuring air and gas purification systems, paired with strong CTAs like “Request a Quote” or “Contact Us for Solutions.” The banner should align with the vibrant red and yellow tones in the Flo7K3 logo.
• Key Product Categories: Introduce the main product categories with icons or images linked to individual product pages.
• Flo7K3 Expertise Section: A section emphasising the company’s role as a trusted distributor, backed by experience and a strong partnership network.
• Why Choose Flo7K3: Highlight 3-4 major benefits, such as “Quick Delivery,” “Expert Consultation,” and “Innovative Technology.”
• Client Testimonials/Partners: Space for customer feedback, testimonials, or logos of partner companies to build trust.
• Newsletter or Enquiry Form: Place a compact form for capturing visitor details for quotes, enquiries, or subscriptions.
2. Product Pages:
• Category Pages: Create well-structured product category pages (e.g., Air Filtration Systems, Nitrogen Generators) similar to industry-standard designs. Each category page should feature professional imagery, short product descriptions, and links to detail pages.
• Product Detail Pages: Each product page will contain:
• High-quality images of the product.
• Detailed specifications, technical descriptions, and features.
• Options to download datasheets or brochures (PDF format).
• Clear CTAs to request a quote or contact sales.
• Product Comparison Tool (Optional): Allow users to compare multiple products, emphasising key features and specifications.
3. About Flo7K3 Page:
• Provide an overview of Flo7K3’s history, mission, and the value it provides as a leading distributor.
• Highlight industry expertise, the partnership network, and any accolades or certifications.
• Mention any regional advantages or special services (e.g., fast delivery times, on-site consultation).
4. Contact Us Page:
• Clean and Simple Form: Include fields for general inquiries or specific product requests.
• Contact Information: Display the company’s, email address info@flo7k3.co.uk.
5. Additional Functionalities:
• Responsive Design: Ensure the design is fully responsive, optimised for mobile, tablet, and desktop viewing.
• SEO Optimisation: Include best practices for search engine optimization (SEO), including clean URLs, meta tags, and image alt text.
• Fast Loading Speed: Optimise images, scripts, and code for fast loading times to improve user experience.
• Social Media Integration: Provide links to social media profiles (if applicable) and potentially include a feed for recent updates.
• Optional Blog: Create a blog space for sharing industry news, product updates, or educational content to engage with visitors and improve SEO.
Style Guide:
1. Color Palette:
• Use colors consistent with the Flo7K3 logo: Red (#FF0000) and Yellow (#FFD700) as primary colors. Incorporate neutral colors (such as white, gray, or black) for balance and readability.
• Accent colors may be introduced for subtle highlights, but the focus should be on the bold, energetic color scheme of Flo7K3.
2. Typography:
• Primary Font for Headings: A bold, modern sans-serif font that complements the strong branding of Flo7K3.
• Secondary Font for Body Text: Clean, easy-to-read sans-serif or serif font for optimal readability across devices.
• Typography Emphasis: Use large, bold typography for headlines to match the boldness of the logo and brand identity.
3. Imagery:
• Use high-quality industrial and technical imagery that reflects the air and gas purification products Flo7K3 distributes.
• Incorporate imagery showing products in action, e.g., in industrial settings or installations.
• Avoid clutter; ensure images are used to enhance user understanding, not overwhelm.
4. Icons:
• Utilise modern, flat-style icons that align with the clean and professional image of Flo7K3. Icons could represent services such as “Fast Delivery,” “Expert Support,” and “High-Quality Products.”
Functionality Requirements:
1. Content Management System (CMS): Build the site using WordPress for easy content management, allowing Flo7K3 staff to update content, product information, and blog posts.
2. Quote Request Integration: Ensure the site has a functional and easy-to-access “Request a Quote” form that appears on every product and service page.
3. Customer Support Section: Optionally include a section for FAQs, product guides, or a knowledge base to support customers and prospects.
4. Security: Implement SSL encryption and ensure that other security best practices (e.g., spam prevention for forms) are followed.
5. Multilingual Support (Optional): Provide the option to support multiple languages, depending on the regional scope of Flo7K3’s distribution services.
Deliverables:
• WordPress template with a homepage, product pages, about section, and contact page.
• SEO-friendly and responsive design.
• Clear CTAs for lead generation (e.g., “Request a Quote”).
• User-friendly interface for both desktop and mobile devices.
Inspiration/Competitors:
• Competitor Analysis: Research similar distributors in the air and gas purification industry for design inspiration.
• Brand Consistency: Ensure Flo7K3’s bold branding is prominent and differentiates it from competitors.
Target Market(s)
Food & Beverage manufacturers, Laser Cutting, Electronics manufacturers, General Industrial Manufacturers

```html
<!DOCTYPE html>
<html lang="en">
<head>
<meta charset="utf-8">
<title>Flo7K3 – About and Contact pages</title>
<link href="https://fonts.googleapis.com/css2?family=Work+Sans:wght@400;500;600;700;800&display=swap" rel="stylesheet">
<style>
:root{
  --backdrop:#C6871F;
  --page:#F1F1F1;
  --yellow:#FFC107;
  --red:#FF2A22;
  --ink:#111111;
  --muted:#333333;
  --white:#FFFFFF;
}
*{margin:0;padding:0;box-sizing:border-box}
html,body{width:1200px;height:1200px;overflow:hidden}
body{background:var(--backdrop);font-family:"Work Sans",sans-serif;color:var(--ink);position:relative}
.page{position:absolute;width:461px;background:var(--page);overflow:hidden}
.page--about{left:140px;top:225px;height:792px}
.page--contact{left:629px;top:247px;height:750px}
.page *{position:absolute}
.page p,.page li,.page span,.page ul,.page strong{position:static}
.brand{font-weight:800;font-size:15px;color:var(--red);letter-spacing:-.2px;line-height:1;white-space:nowrap}
.brand--light{color:var(--white)}
.site-header .brand{left:48px;top:16px}
.nav{top:22px;display:flex;gap:6px;font-size:3.6px;font-weight:500;text-transform:uppercase;letter-spacing:.1px;white-space:nowrap}
.nav .strong{font-weight:700}
.nav .active{color:var(--red);font-weight:700}
.header-icons{top:19px;display:flex;gap:9px;align-items:center;white-space:nowrap}
.header-icons svg{position:static;width:8px;height:8px}
.header-icons span{font-size:3px;color:#555}
.breadcrumb{left:48px;top:50px;font-size:7.5px;font-weight:500;white-space:nowrap}
.breadcrumb .current{color:var(--red)}
.hero{left:0;top:66px;width:461px;height:165px}
.hero-media{right:0;top:0;height:165px}
.hero-panel{left:0;top:0;height:165px;background:var(--yellow);border-top-right-radius:26px}
.hero-title{left:48px;font-size:15px;font-weight:600;line-height:18px}
.hero-text{left:48px;font-size:7.8px;line-height:10px;color:var(--muted)}
.section-title{left:48px;font-size:14.5px;font-weight:600;white-space:nowrap}
.body-copy{left:48px;width:365px;font-size:8.2px;line-height:10.1px;color:var(--muted)}
.footer{left:0;width:461px;background:var(--yellow);border-top-left-radius:52px}
.footer .brand{left:48px}
.footer-blurb{left:48px;width:64px;font-size:3.8px;line-height:4.6px;color:var(--red)}
.footer-head{font-size:7.2px;font-weight:600;white-space:nowrap}
.footer-item{font-size:3.9px;line-height:4.8px;color:var(--red);white-space:nowrap}
.footer-icon{width:8px;height:8px}
.socials{display:flex;gap:10px}
.socials i{position:static;display:block;width:13px;height:13px;border-radius:50%;background:var(--red)}
.field-label{font-size:8px;color:var(--muted);white-space:nowrap}
.field-line{height:0;border-top:.8px solid var(--red)}
.submit{left:150px;top:524px;width:87px;height:27px;background:var(--red);border-radius:4px;color:var(--white);font-size:7.5px;font-weight:600;display:flex;align-items:center;justify-content:center}
.info-head{left:258px;font-size:8px;font-weight:600;white-space:nowrap}
.info-text{left:258px;width:165px;font-size:8px;line-height:10.1px;color:var(--muted)}
.info-text ul{list-style:none;padding-left:6px}
.info-text li::before{content:"•";margin-right:4px;font-size:6px}
</style>
</head>
<body>

<section class="page page--about">
  <header class="site-header">
    <div class="brand">Flo7K3</div>
    <nav class="nav" style="left:184px">
      <span>Home</span><span class="strong">Product</span><span class="active">About us</span><span>Services</span><span>Blog</span><span>Contact us</span>
    </nav>
    <div class="header-icons" style="left:372px">
      <svg viewBox="0 0 16 16" fill="none" stroke="#111" stroke-width="1.3"><circle cx="8" cy="5" r="3"/><path d="M2.5 15c0-3.5 2.5-5.5 5.5-5.5s5.5 2 5.5 5.5z"/></svg>
      <svg viewBox="0 0 16 16" fill="none" stroke="#111" stroke-width="1.3"><rect x="2" y="5" width="12" height="10" rx="1"/><path d="M5.5 5V3.5a2.5 2.5 0 0 1 5 0V5"/></svg>
      <span>GBP</span>
    </div>
  </header>
  <div class="breadcrumb">Home &gt; <span class="current">About</span></div>

  <div class="hero">
    <div class="hero-media" role="img" aria-label="Photo of a technician in safety glasses and cap adjusting yellow gas pipe valves" style="width:300px;background:linear-gradient(120deg,#c9a23a 0%,#8a7a5a 40%,#4a4f58 75%,#2a2e36 100%)"></div>
    <div class="hero-panel" style="width:188px"></div>
    <h1 class="hero-title" style="top:51px">About<br>Flo7K3</h1>
    <p class="hero-text" style="top:115px;position:absolute;width:110px">Your Trusted Nitrogen Generation Partner</p>
  </div>

  <h2 class="section-title" style="top:253px">Overview:</h2>
  <div class="body-copy" style="top:287px">
    <p>Flo7K3 has been at the forefront of nitrogen generation solutions for over a decade, providing cutting-edge products and exceptional service to a wide range of industries. From food and beverage manufacturing to electronics and industrial applications, we specialize in delivering on-site nitrogen production systems that increase efficiency and reduce costs.</p>
    <p>As a leading distributor, we pride ourselves on offering reliable, innovative solutions that help businesses stay ahead in their operations. Our commitment to quality and customer satisfaction has earned us a solid reputation across the globe.</p>
  </div>

  <h2 class="section-title" style="top:389px">Our Mission:</h2>
  <div class="body-copy" style="top:423px">
    <p>At Flo7K3, our mission is to deliver sustainable, efficient, and cost-effective nitrogen solutions that empower businesses to optimize their processes. We believe in combining advanced technology with superior service to ensure that our clients receive the best in the industry.</p>
  </div>

  <h2 class="section-title" style="top:488px">Industry Expertise:</h2>
  <div class="body-copy" style="top:523px">
    <p>With years of experience in the air and gas purification sector, Flo7K3 has developed deep expertise in nitrogen generation. Our team of highly qualified engineers and technicians ensures seamless installation, maintenance, and technical support for every system we provide. We work closely with industry leaders and innovators to stay at the forefront of nitrogen technology, offering our clients the latest advancements in PSA and membrane-based solutions.</p>
  </div>

  <footer class="footer" style="top:622px;height:170px">
    <div class="brand brand--light" style="top:45px">Flo7K3</div>
    <p class="footer-blurb" style="top:70px;position:absolute">You minim mollit non deserunt ullamco est sit aliqua dolor do amet sint. Velit officia consequat duis</p>

    <div class="footer-head" style="left:153px;top:56px">Get In Touch</div>
    <svg class="footer-icon" style="left:152px;top:75px" viewBox="0 0 16 16" fill="none" stroke="#FF2A22" stroke-width="1.4"><path d="M8 15s5-5 5-8.5a5 5 0 0 0-10 0C3 10 8 15 8 15z"/><circle cx="8" cy="6.5" r="1.8"/></svg>
    <div class="footer-item" style="left:171px;top:76px">2280 Millbrook Rd.<br>Harlow Vale, Essex<br>40217</div>
    <svg class="footer-icon" style="left:152px;top:104px" viewBox="0 0 16 16" fill="none" stroke="#FF2A22" stroke-width="1.4"><rect x="2" y="3" width="12" height="10" rx="2"/><path d="M3 5l5 4 5-4"/></svg>
    <div class="footer-item" style="left:171px;top:105px">info@flo7k3.co.uk</div>
    <svg class="footer-icon" style="left:152px;top:127px" viewBox="0 0 16 16" fill="none" stroke="#FF2A22" stroke-width="1.4"><path d="M4 2h4l1 3-2 1.5a7 7 0 0 0 3.5 3.5L12 8l3 1v4c0 .5-.5 1-1 1A12 12 0 0 1 2 3c0-.5.5-1 1-1z"/></svg>
    <div class="footer-item" style="left:171px;top:128px">(207) 555-0143<br>(702) 555-0176</div>

    <div class="footer-head" style="left:245px;top:56px">Explore Link</div>
    <div class="footer-item" style="left:246px;top:76px">About Us</div>
    <div class="footer-item" style="left:246px;top:91px">Career</div>
    <div class="footer-item" style="left:246px;top:105px">FAQ</div>
    <div class="footer-item" style="left:246px;top:120px">Blog</div>
    <div class="footer-item" style="left:246px;top:136px">Product</div>

    <div class="footer-head" style="left:327px;top:56px">Office Time</div>
    <div class="footer-item" style="left:328px;top:76px">Mon-Fri: 8:30AM - 5.30PM<br>Saturday: 9:00AM - 1.00PM<br>Sunday: Closed</div>
    <div class="socials" style="left:328px;top:107px"><i></i><i></i><i></i></div>
  </footer>
</section>

<section class="page page--contact">
  <header class="site-header">
    <div class="brand">Flo7K3</div>
    <nav class="nav" style="left:184px">
      <span>Home</span><span class="strong">Product</span><span>About us</span><span>Services</span><span>Blog</span><span class="active">Contact us</span>
    </nav>
    <div class="header-icons" style="left:372px">
      <svg viewBox="0 0 16 16" fill="none" stroke="#111" stroke-width="1.3"><circle cx="8" cy="5" r="3"/><path d="M2.5 15c0-3.5 2.5-5.5 5.5-5.5s5.5 2 5.5 5.5z"/></svg>
      <svg viewBox="0 0 16 16" fill="none" stroke="#111" stroke-width="1.3"><rect x="2" y="5" width="12" height="10" rx="1"/><path d="M5.5 5V3.5a2.5 2.5 0 0 1 5 0V5"/></svg>
      <span>GBP</span>
    </div>
  </header>
  <div class="breadcrumb">Home &gt; <span class="current">Contact us</span></div>

  <div class="hero">
    <div class="hero-media" role="img" aria-label="Photo of a worker in a yellow hard hat and overalls with arms crossed" style="width:200px;background:radial-gradient(ellipse at 65% 65%,#d9b43a 0%,#c98a30 22%,#FF2A22 55%)"></div>
    <div class="hero-panel" style="width:275px"></div>
    <h1 class="hero-title" style="top:20px">Get in<br>Touch with<br>Flo7K3</h1>
    <p class="hero-text" style="top:101px;position:absolute;width:200px">We’re here to help you find the perfect nitrogen solution for your business. Whether you have a general inquiry or need specific product information, reach out to our team.</p>
  </div>

  <h2 class="section-title" style="top:253px">Contact Form:</h2>
  <div class="body-copy" style="top:283px;width:190px;font-size:8px">
    <p><strong style="color:var(--ink);font-weight:600">General Inquiry Form:</strong><br>Please fill out the form below, and our team will get back to you as soon as possible.</p>
  </div>

  <div class="field-label" style="left:48px;top:336px">Name :</div>
  <div class="field-line" style="left:48px;top:358px;width:87px"></div>
  <div class="field-label" style="left:150px;top:336px">Company Name:</div>
  <div class="field-line" style="left:150px;top:358px;width:87px"></div>
  <div class="field-label" style="left:48px;top:376px">Email :</div>
  <div class="field-line" style="left:48px;top:400px;width:87px"></div>
  <div class="field-label" style="left:150px;top:376px">Email :</div>
  <div class="field-line" style="left:150px;top:400px;width:87px"></div>
  <div class="field-label" style="left:48px;top:423px">Message</div>
  <div class="field-line" style="left:48px;top:513px;width:189px"></div>
  <div class="submit">Submit</div>

  <div class="info-head" style="top:338px">Contact Information:</div>
  <div class="info-text" style="top:357px">
    <p>For immediate assistance, feel free to reach out directly:</p>
    <ul><li>Phone: +44 1632 960418</li><li>Email: info@flo7k3.co.uk</li></ul>
  </div>
  <div class="info-head" style="top:409px">Office Address:</div>
  <div class="info-text" style="top:430px">
    <p>Flo7K3 Headquarters<br>48 Kestrel Works, Riverside Trade Park<br>Leeds, UK</p>
  </div>

  <footer class="footer" style="top:584px;height:166px">
    <div class="brand brand--light" style="top:45px">Flo7K3</div>
    <p class="footer-blurb" style="top:70px;position:absolute">You minim mollit non deserunt ullamco est sit aliqua dolor do amet sint. Velit officia consequat duis</p>

    <div class="footer-head" style="left:153px;top:50px">Get In Touch</div>
    <svg class="footer-icon" style="left:152px;top:69px" viewBox="0 0 16 16" fill="none" stroke="#FF2A22" stroke-width="1.4"><path d="M8 15s5-5 5-8.5a5 5 0 0 0-10 0C3 10 8 15 8 15z"/><circle cx="8" cy="6.5" r="1.8"/></svg>
    <div class="footer-item" style="left:171px;top:70px">2280 Millbrook Rd.<br>Harlow Vale, Essex<br>40217</div>
    <svg class="footer-icon" style="left:152px;top:98px" viewBox="0 0 16 16" fill="none" stroke="#FF2A22" stroke-width="1.4"><rect x="2" y="3" width="12" height="10" rx="2"/><path d="M3 5l5 4 5-4"/></svg>
    <div class="footer-item" style="left:171px;top:99px">info@flo7k3.co.uk</div>
    <svg class="footer-icon" style="left:152px;top:121px" viewBox="0 0 16 16" fill="none" stroke="#FF2A22" stroke-width="1.4"><path d="M4 2h4l1 3-2 1.5a7 7 0 0 0 3.5 3.5L12 8l3 1v4c0 .5-.5 1-1 1A12 12 0 0 1 2 3c0-.5.5-1 1-1z"/></svg>
    <div class="footer-item" style="left:171px;top:122px">(207) 555-0143<br>(702) 555-0176</div>

    <div class="footer-head" style="left:245px;top:50px">Explore Link</div>
    <div class="footer-item" style="left:246px;top:70px">About Us</div>
    <div class="footer-item" style="left:246px;top:85px">Career</div>
    <div class="footer-item" style="left:246px;top:99px">FAQ</div>
    <div class="footer-item" style="left:246px;top:114px">Blog</div>
    <div class="footer-item" style="left:246px;top:130px">Product</div>

    <div class="footer-head" style="left:327px;top:50px">Office Time</div>
    <div class="footer-item" style="left:328px;top:70px">Mon-Fri: 8:30AM - 5.30PM<br>Saturday: 9:00AM - 1.00PM<br>Sunday: Closed</div>
    <div class="socials" style="left:328px;top:101px"><i></i><i></i><i></i></div>
  </footer>
</section>

</body>
</html>
```